CANNABIS BASED BUSINESS CARD DESIGN AND CREATION

WE ARE A PRIVATELY OWNED INVESTMENT CORPORATION. WE PRIMARILY INVEST IN LEGAL PUBLICALLY TRADED CANNABIS COMPANIES THAT ARE TRADED THROUGH THE OTC OR VOLTRIX. WE OFFER THE PUBLIC AN OPPORTUNITY TO PARTICIPATE DIRECTLY WITH THESE COMPANIES FOR NO FEES, NO COMMISSIONS AND IN DEPTH RESEARCH ON EVERY COMPANY PROFILE. WE ARE ALSO PRO FEDERAL LEGALIZATION AND WILL APPLY FOR CULTIVATION AND DISPENSARY LICENSES WHEN THEY BECOME AVAILABLE.

Target Market(s)

30-60 FEMALE AND MALE INVESTORS

Industry/Entity Type

Business

Contact Information for Business Card

EDS CAPITAL GROUP CORPERIN D SLAUGHTER(469) 426-6302ERIN@EDSCAPITALGROUP.COM

Font styles to use
Decorative

Requirements
Must have
• COMPANY LOGO
• CANNABIS LOGO
Nice to have
• MODERN FONT AND LOGOS

```html
<!DOCTYPE html>
<html lang="en">
<head>
<meta charset="utf-8">
<title>TQM Capital Group Corp – Business Card</title>
<link href="https://fonts.googleapis.com/css2?family=Lato:wght@400;700&display=swap" rel="stylesheet">
<style>
  :root {
    --stage: #5f6b1a;
    --card-dark: #0b0b0b;
    --card-mid: #1c1c1c;
    --leaf-green: #2fb34a;
    --name-red: #e0262b;
    --text-light: #d6d6d6;
    --rule: #2e2e2e;
    --decor: #1f1f1f;
  }
  * { margin: 0; padding: 0; box-sizing: border-box; }
  html, body {
    width: 1200px; height: 900px; overflow: hidden;
    background: var(--stage);
    font-family: "Lato", Arial, sans-serif;
  }
  .stage { position: relative; width: 1200px; height: 900px; }
  .card {
    position: absolute; width: 640px; height: 366px;
    border-radius: 22px; overflow: hidden;
    background: linear-gradient(135deg, var(--card-mid) 0%, var(--card-dark) 55%, var(--card-dark) 100%);
  }
  .card-front { left: 90px; top: 70px; }
  .card-back { left: 470px; top: 464px; }

  .leaf-decoration {
    position: absolute; right: 40px; top: 30px;
    width: 250px; height: 260px; border-radius: 50%;
    background: radial-gradient(circle, var(--decor) 0%, rgba(31,31,31,0) 70%);
  }

  .brand {
    position: absolute; display: flex; flex-direction: column; align-items: center;
    color: var(--leaf-green); font-weight: 700; text-align: center;
  }
  .brand-mark {
    width: 22px; height: 22px; border-radius: 50%;
    background: var(--leaf-green); margin-bottom: 14px;
  }
  .card-front .brand { left: 0; right: 0; top: 110px; }
  .card-front .brand-name { font-size: 58px; letter-spacing: 3px; line-height: 1; }
  .card-front .brand-sub { font-size: 30px; letter-spacing: 4px; margin-top: 10px; }
  .card-front .brand-mark { width: 34px; height: 34px; }

  .card-back .brand { right: 50px; top: 42px; width: 240px; }
  .card-back .brand-name { font-size: 38px; letter-spacing: 2px; line-height: 1; }
  .card-back .brand-sub { font-size: 17px; letter-spacing: 2px; margin-top: 6px; }

  .divider { position: absolute; height: 1px; background: var(--rule); }
  .divider-contact { right: 40px; top: 200px; width: 250px; }
  .divider-name { left: 40px; top: 324px; width: 300px; }

  .holder-name {
    position: absolute; left: 40px; top: 294px;
    color: var(--name-red); font-size: 18px; letter-spacing: 0.5px;
  }

  .contact-list {
    position: absolute; right: 40px; top: 222px; width: 250px;
    list-style: none; color: var(--text-light); font-size: 13px;
  }
  .contact-list li { display: flex; align-items: center; gap: 10px; margin-bottom: 9px; }
  .contact-list svg { width: 14px; height: 14px; fill: var(--leaf-green); flex: none; }
</style>
</head>
<body>
<main class="stage">

  <section class="card card-front" aria-label="Card front">
    <div class="leaf-decoration" role="img" aria-label="Faint cannabis leaf decoration"></div>
    <div class="brand">
      <span class="brand-mark"></span>
      <span class="brand-name">TQM</span>
      <span class="brand-sub">CAPITAL GROUP CORP</span>
    </div>
  </section>

  <section class="card card-back" aria-label="Card back">
    <div class="brand">
      <span class="brand-mark"></span>
      <span class="brand-name">TQM</span>
      <span class="brand-sub">CAPITAL GROUP CORP</span>
    </div>
    <div class="divider divider-contact"></div>

    <ul class="contact-list">
      <li>
        <svg viewBox="0 0 24 24" aria-hidden="true"><path d="M6.6 10.8a15 15 0 0 0 6.6 6.6l2.2-2.2a1 1 0 0 1 1-.25 11.4 11.4 0 0 0 3.6.57 1 1 0 0 1 1 1V20a1 1 0 0 1-1 1A17 17 0 0 1 3 4a1 1 0 0 1 1-1h3.5a1 1 0 0 1 1 1c0 1.25.2 2.45.57 3.57a1 1 0 0 1-.25 1z"/></svg>
        <span>(555) 013-4478</span>
      </li>
      <li>
        <svg viewBox="0 0 24 24" aria-hidden="true"><path d="M2 5h20v14H2z M2 5l10 8 10-8" /></svg>
        <span>marla@tqmcapitalgroup-demo.com</span>
      </li>
      <li>
        <svg viewBox="0 0 24 24" aria-hidden="true"><path d="M10 14a4 4 0 0 1 0-5.7l3-3a4 4 0 0 1 5.7 5.7l-1.5 1.5-1.4-1.4 1.5-1.5a2 2 0 0 0-2.9-2.9l-3 3a2 2 0 0 0 0 2.9zM14 10a4 4 0 0 1 0 5.7l-3 3a4 4 0 0 1-5.7-5.7l1.5-1.5 1.4 1.4-1.5 1.5a2 2 0 0 0 2.9 2.9l3-3a2 2 0 0 0 0-2.9z"/></svg>
        <span>www.tqmcapitalgroup-demo.com</span>
      </li>
    </ul>

    <p class="holder-name">MARLA J PENDLEBURY</p>
    <div class="divider divider-name"></div>
  </section>

</main>
</body>
</html>
```